business card deign

Logo needs the following on it.
1. attached logo
2. Tagline - "If it keeps a drink cold or the party going...we do it!"
3. Name- Dalton Pikes, Founder and CPO
4. Address - 412 E. Carver Avenue, Ste 2207, Tampa, FL. 33917
5. Phone - 555.318.4726

```html
<!DOCTYPE html>
<html lang="en">
<head>
<meta charset="utf-8">
<title>Hopwell Business Card</title>
<link href="https://fonts.googleapis.com/css2?family=Montserrat:wght@400;700&display=swap" rel="stylesheet">
<style>
  :root {
    --page: #e9e6e1;
    --card: #ffffff;
    --ink: #0b0b0b;
    --grey: #a9a9a9;
    --soft-shadow: rgba(0, 0, 0, 0.18);
  }
  * { box-sizing: border-box; margin: 0; padding: 0; }
  html, body {
    width: 1200px;
    height: 931px;
    overflow: hidden;
    background: var(--page);
    font-family: "Montserrat", sans-serif;
    color: var(--ink);
  }
  .sheet {
    position: relative;
    width: 1200px;
    height: 931px;
  }
  .card {
    position: absolute;
    width: 700px;
    height: 400px;
    background: var(--card);
    border-radius: 22px;
    overflow: hidden;
    box-shadow: 0 10px 24px var(--soft-shadow);
  }
  .card--front { left: 250px; top: 45px; }
  .card--back  { left: 250px; top: 486px; }

  .wordmark {
    display: flex;
    align-items: center;
    gap: 14px;
    font-weight: 700;
    letter-spacing: 0.32em;
    color: var(--ink);
  }
  .wordmark__dot {
    width: 22px;
    height: 22px;
    border-radius: 50%;
    background: var(--ink);
    flex: none;
  }
  .card--front .wordmark {
    position: absolute;
    left: 50%;
    top: 50%;
    transform: translate(-50%, -50%);
    font-size: 46px;
  }
  .card--back .wordmark {
    position: absolute;
    left: 40px;
    top: 150px;
    font-size: 32px;
    letter-spacing: 0.22em;
  }
  .card--back .wordmark__dot { width: 16px; height: 16px; }

  .divider {
    position: absolute;
    left: 330px;
    top: 88px;
    width: 1.5px;
    height: 150px;
    background: var(--ink);
  }
  .contact {
    position: absolute;
    left: 358px;
    top: 74px;
  }
  .contact__name {
    font-weight: 700;
    font-size: 22px;
    letter-spacing: 0.02em;
    text-transform: uppercase;
  }
  .contact__title {
    font-size: 18px;
    margin-top: 2px;
  }
  .contact__list {
    list-style: none;
    margin-top: 18px;
    font-size: 16px;
    line-height: 1.45;
  }
  .contact__item {
    display: flex;
    align-items: flex-start;
    gap: 10px;
  }
  .contact__icon {
    width: 16px;
    height: 16px;
    margin-top: 3px;
    flex: none;
  }
  .wave {
    position: absolute;
    left: 0;
    top: 0;
    width: 700px;
    height: 400px;
  }
</style>
</head>
<body>
<main class="sheet">
  <section class="card card--front" aria-label="Card front">
    <div class="wordmark"><span class="wordmark__dot"></span>HOPWELL</div>
  </section>

  <section class="card card--back" aria-label="Card back">
    <svg class="wave" viewBox="0 0 700 400" aria-hidden="true">
      <path d="M0,358 C150,346 300,350 440,298 C560,250 630,216 700,202 L700,214 C630,228 560,262 440,310 C300,362 150,358 0,370 Z" fill="var(--grey)"/>
      <path d="M0,380 C150,368 300,372 440,320 C560,272 630,238 700,224 L700,400 L0,400 Z" fill="var(--ink)"/>
      <path d="M0,390 C150,378 300,382 442,330 C562,282 632,248 700,234" fill="none" stroke="var(--card)" stroke-width="2"/>
    </svg>

    <div class="wordmark"><span class="wordmark__dot"></span>HOPWELL</div>
    <div class="divider"></div>

    <div class="contact">
      <p class="contact__name">Dalton Pikes</p>
      <p class="contact__title">Founder and CPO</p>
      <ul class="contact__list">
        <li class="contact__item">
          <svg class="contact__icon" viewBox="0 0 16 16" aria-hidden="true">
            <path d="M1 5 C1 2 15 2 15 5 L15 6.5 L11 6.5 L11 5 L5 5 L5 6.5 L1 6.5 Z" fill="var(--ink)"/>
            <path d="M3 8 L13 8 L14.5 15 L1.5 15 Z" fill="var(--ink)"/>
            <circle cx="8" cy="11.5" r="1.8" fill="var(--card)"/>
          </svg>
          <span>555.318.4726</span>
        </li>
        <li class="contact__item">
          <svg class="contact__icon" viewBox="0 0 16 16" aria-hidden="true">
            <path d="M8 0.5 C4.7 0.5 2.5 2.9 2.5 5.8 C2.5 9.6 8 15.5 8 15.5 C8 15.5 13.5 9.6 13.5 5.8 C13.5 2.9 11.3 0.5 8 0.5 Z" fill="var(--ink)"/>
            <circle cx="8" cy="5.8" r="2.2" fill="var(--card)"/>
          </svg>
          <span>412 E. Carver Avenue, Ste<br>2207, Tampa, FL. 33917</span>
        </li>
      </ul>
    </div>
  </section>
</main>
</body>
</html>
```